Business card for medical clinic

I need an upmarket, modern medical/health business card for my clinic

Contact Information for Business Card

name, address, email, qr code

```html
<!DOCTYPE html>
<html lang="en">
<head>
<meta charset="utf-8">
<title>Meridia Health Clinic – Business Card</title>
<link href="https://fonts.googleapis.com/css2?family=Montserrat:wght@400;500;600;700;800&display=swap" rel="stylesheet">
<style>
  :root {
    --bg: #d9dde2;
    --card: #ffffff;
    --navy: #13466f;
    --deep: #0f5a86;
    --ocean: #1f8cc0;
    --sky: #29abe2;
    --ink: #1f2428;
    --white: #ffffff;
  }
  * { margin: 0; padding: 0; box-sizing: border-box; }
  html, body {
    width: 1200px; height: 880px; overflow: hidden;
    background: var(--bg);
    font-family: "Montserrat", sans-serif;
  }
  .canvas { position: relative; width: 1200px; height: 880px; }
  .card {
    position: absolute; left: 300px; width: 600px; height: 343px;
    background: var(--card); border-radius: 22px; overflow: hidden;
    box-shadow: 0 10px 28px rgba(0,0,0,0.18);
  }
  .card--front { top: 72px; }
  .card--back { top: 465px; }

  .brand {
    position: absolute; display: flex; align-items: center;
    color: var(--navy); font-weight: 600; letter-spacing: 0.04em;
    text-transform: uppercase; white-space: nowrap;
  }
  .brand__dot { border-radius: 50%; border: 3px solid var(--sky); flex: none; }
  .card--front .brand {
    left: 0; right: 0; top: 140px; justify-content: center;
    font-size: 26px; gap: 16px;
  }
  .card--front .brand__dot { width: 54px; height: 54px; }
  .card--back .brand { left: 40px; top: 98px; font-size: 20px; gap: 12px; }
  .card--back .brand__dot { width: 36px; height: 36px; }

  .wave { position: absolute; inset: 0; width: 600px; height: 343px; }

  .edge-tab {
    position: absolute; right: 0; top: 18px; width: 12px; height: 40px;
    background: var(--sky);
  }
  .person { position: absolute; right: 36px; top: 22px; text-align: right; }
  .person__name {
    color: var(--sky); font-weight: 800; font-size: 24px; letter-spacing: 0.02em;
  }
  .person__role { color: var(--ink); font-weight: 500; font-size: 14px; margin-top: 2px; }
  .contact {
    position: absolute; right: 24px; top: 168px; text-align: right;
    color: var(--white); font-size: 13px; line-height: 1.5; font-weight: 400;
    list-style: none;
  }
  .contact__address { margin-bottom: 10px; margin-right: 22px; }
  .contact__row { display: flex; justify-content: flex-end; align-items: center; gap: 8px; }
  .contact__row svg { width: 14px; height: 14px; flex: none; }
</style>
</head>
<body>
<main class="canvas">

  <section class="card card--front" aria-label="Card front">
    <div class="brand"><span class="brand__dot"></span>Meridia Health Clinic</div>
  </section>

  <section class="card card--back" aria-label="Card back">
    <svg class="wave" viewBox="0 0 600 343" aria-hidden="true">
      <defs>
        <linearGradient id="deepFill" x1="0" y1="0" x2="0.4" y2="1">
          <stop offset="0" stop-color="#0f4f7c"/>
          <stop offset="1" stop-color="#2190c4"/>
        </linearGradient>
      </defs>
      <path d="M600,62 C430,62 372,130 332,202 C288,280 180,300 0,282 L0,343 L600,343 Z" fill="var(--sky)"/>
      <path d="M600,76 C436,76 382,140 342,212 C297,288 186,310 0,294 L0,343 L600,343 Z" fill="var(--white)"/>
      <path d="M600,88 C440,88 390,150 350,220 C305,295 190,318 0,305 L0,343 L600,343 Z" fill="url(#deepFill)"/>
    </svg>

    <div class="brand"><span class="brand__dot"></span>Meridia Health Clinic</div>

    <span class="edge-tab"></span>
    <div class="person">
      <p class="person__name">DANIEL HART</p>
      <p class="person__role">Managing Director</p>
    </div>

    <ul class="contact">
      <li class="contact__address">Your address, City<br>State, Zip 1234</li>
      <li class="contact__row">123 456 789
        <svg viewBox="0 0 16 16"><path fill="#fff" d="M4 1l3 3-2 2c1 2 3 4 5 5l2-2 3 3-2 3C7 14 2 9 1 3z"/></svg></li>
      <li class="contact__row">info@yourgmail.com
        <svg viewBox="0 0 16 16"><rect x="1" y="3" width="14" height="10" rx="1" fill="#fff"/><path d="M1 4l7 5 7-5" fill="none" stroke="#1f8cc0" stroke-width="1.4"/></svg></li>
      <li class="contact__row">www.yourwebsite.com
        <svg viewBox="0 0 16 16"><circle cx="8" cy="8" r="7" fill="#fff"/><path d="M1 8h14M8 1c3 3 3 11 0 14M8 1c-3 3-3 11 0 14" fill="none" stroke="#1f8cc0" stroke-width="1"/></svg></li>
    </ul>
  </section>

</main>
</body>
</html>
```